Floor Inspections and Consulting

We provide inspections and consulting services on various floor coverings, e.g. carpet, hardwood, etc. We also do expert witness work for attorneys due to floor covering failures. We current have a logo, just need it incorporated into a new design. I have examples of cards I have found on the internet that capture my attention and make a statement. I have included our original business card, which in my opinion is terrible, but it does have our logo on it.

```html
<!DOCTYPE html>
<html lang="en">
<head>
<meta charset="utf-8">
<title>Keystone Floor Inspections – Business Card</title>
<link href="https://fonts.googleapis.com/css2?family=Krona+One&family=Archivo:wght@700;800&family=Arimo:wght@400&display=swap" rel="stylesheet">
<style>
  :root {
    --bg: #3a3a3c;
    --card-black: #111112;
    --orange: #e0501a;
    --orange-deep: #c9400f;
    --charcoal: #2a2a2c;
    --grey: #6d6d6f;
    --white: #ffffff;
  }
  * { margin: 0; padding: 0; box-sizing: border-box; }
  html, body { width: 1200px; height: 1015px; overflow: hidden; }
  body {
    background: var(--bg);
    position: relative;
    font-family: "Arimo", Arial, sans-serif;
  }
  .card {
    position: absolute;
    left: 250px;
    width: 700px;
    height: 400px;
    overflow: hidden;
    box-shadow: 0 10px 30px rgba(0,0,0,.35);
  }
  .card--front { top: 70px; background: var(--card-black); }
  .card--back {
    top: 545px;
    background: linear-gradient(160deg, var(--orange) 0%, var(--orange-deep) 100%);
  }
  .edge-bar { position: absolute; width: 14px; height: 90px; }
  .edge-bar--right { right: 0; top: 40px; }
  .edge-bar--left { left: 0; bottom: 70px; }
  .card--front .edge-bar { background: var(--orange); }
  .card--back .edge-bar { background: var(--charcoal); }

  .brand {
    position: absolute;
    display: flex;
    align-items: center;
    gap: 18px;
  }
  .brand__square { width: 54px; height: 54px; flex: none; }
  .brand__name {
    font-family: "Krona One", "Arial Black", sans-serif;
    font-size: 26px;
    line-height: 1.15;
    letter-spacing: 1px;
    text-transform: uppercase;
  }
  .card--front .brand { left: 150px; top: 120px; }
  .card--front .brand__square { background: var(--orange); }
  .card--front .brand__name { color: var(--orange); }

  .tagline {
    position: absolute;
    left: 150px;
    top: 250px;
    font-family: "Archivo", Arial, sans-serif;
    font-weight: 700;
    font-size: 19px;
    color: #d9d9d9;
  }

  .card--back .brand { left: 130px; top: 70px; }
  .card--back .brand__square { background: var(--charcoal); }
  .card--back .brand__name { color: var(--charcoal); }
  .services {
    position: absolute;
    left: 202px;
    top: 182px;
    font-family: "Krona One", "Arial Black", sans-serif;
    font-size: 17px;
    color: var(--white);
    letter-spacing: 1px;
  }

  .contact-left { position: absolute; left: 60px; top: 290px; }
  .contact-right { position: absolute; left: 390px; top: 255px; }
  .contact-row {
    display: flex;
    align-items: center;
    gap: 10px;
    color: var(--white);
    font-size: 17px;
    margin-bottom: 12px;
  }
  .contact-row--name {
    font-family: "Archivo", Arial, sans-serif;
    font-weight: 800;
    font-size: 24px;
    text-transform: uppercase;
  }
  .icon { width: 28px; height: 28px; flex: none; }
</style>
</head>
<body>

  <section class="card card--front">
    <div class="edge-bar edge-bar--right"></div>
    <div class="edge-bar edge-bar--left"></div>
    <div class="brand">
      <div class="brand__square"></div>
      <div class="brand__name">Keystone Floor<br>Inspections</div>
    </div>
    <p class="tagline">Certified Floor Covering Inspection &amp; Consulting</p>
  </section>

  <section class="card card--back">
    <div class="edge-bar edge-bar--right"></div>
    <div class="edge-bar edge-bar--left"></div>
    <div class="brand">
      <div class="brand__square"></div>
      <div class="brand__name">Keystone Floor<br>Inspections</div>
    </div>
    <p class="services">ANALYSIS &amp; CONSULTING</p>

    <div class="contact-right">
      <div class="contact-row">
        <svg class="icon" viewBox="0 0 28 28" aria-hidden="true">
          <circle cx="14" cy="14" r="14" fill="#2a2a2c"/>
          <path d="M9 7.5c1-.6 2 .3 2.5 1.4l.7 1.7c.3.7 0 1.3-.6 1.7l-.8.6c.8 1.8 2.1 3.1 3.9 3.9l.6-.8c.4-.6 1-.9 1.7-.6l1.7.7c1.1.5 2 1.5 1.4 2.5-.9 1.5-2.5 2-4.1 1.4-3.7-1.3-6.5-4.1-7.8-7.8-.6-1.6-.1-3.2 1.4-4.1z" fill="#e0501a"/>
        </svg>
        <span>555-014-2288</span>
      </div>
      <div class="contact-row">
        <svg class="icon" viewBox="0 0 28 28" aria-hidden="true">
          <circle cx="14" cy="14" r="14" fill="#2a2a2c"/>
          <rect x="7" y="9" width="14" height="10" fill="none" stroke="#e0501a" stroke-width="1.6"/>
          <path d="M7 9l7 6 7-6" fill="none" stroke="#e0501a" stroke-width="1.6"/>
        </svg>
        <span>dan@keystonefloors.com</span>
      </div>
    </div>

    <div class="contact-left">
      <div class="contact-row contact-row--name">
        <svg class="icon" viewBox="0 0 28 28" aria-hidden="true">
          <circle cx="14" cy="14" r="14" fill="#2a2a2c"/>
          <circle cx="14" cy="11" r="3.5" fill="none" stroke="#e0501a" stroke-width="1.6"/>
          <path d="M8 20c1-3 3.5-4.5 6-4.5s5 1.5 6 4.5" fill="none" stroke="#e0501a" stroke-width="1.6"/>
        </svg>
        <span>Daniel Marlow</span>
      </div>
      <div class="contact-row">
        <svg class="icon" viewBox="0 0 28 28" aria-hidden="true">
          <circle cx="14" cy="14" r="14" fill="#2a2a2c"/>
          <circle cx="14" cy="14" r="7" fill="none" stroke="#e0501a" stroke-width="1.5"/>
          <ellipse cx="14" cy="14" rx="3" ry="7" fill="none" stroke="#e0501a" stroke-width="1.3"/>
          <path d="M7 14h14M8.5 10.5h11M8.5 17.5h11" stroke="#e0501a" stroke-width="1.2"/>
        </svg>
        <span>www.keystonefloors.com</span>
      </div>
    </div>
  </section>

</body>
</html>
```